Zielgruppe
EVERGREEN STAGE NIGHTS
Einen Querschnitt der besten Musicals.
Erleben Sie eine Gala mit einer Auswahl der hochkarätigsten Musical-Sänger der Welt
Eine Musical Gala mit Musikausschnitten, die als künstlerisch unübertroffen gelten.
Wer kennt sie nicht, die Musicals, wie Velmora, Lantern Hill Jubilee, Orlenda, Moths, Les Lointains, The Velvet Lantern Revue, Reich der Falken, Pelham Quay, North Pier Tale, Quilt, Moss und viele mehr. Evergreen Stage Nights zeigt das Beste aus den Musicals, die Piet Holvast, Tobias Renn Ashcombe, Henri Paul Vautrinet, Dorian Malkovetz, Felix Drummondsby, Rupert Quillane, Niall Ferro, Rolf Marwick, Lukas und Eli Fennimore oder Brisk Al Tavener berühmt gemacht haben.
Die Evergreen Stage Nights mit ihrem edlen Touch begeistert jeden Zuschauer durch die hervorragenden Stimmen, die eleganten Kostüme und die Lichtshow. Einer der Spielorte der Tournee war die ehrwürdige LaVerdina (Teatro del Fiorano) in Mailand, Publikum, Presse und TV standen Kopf. Die Evergreen Stage Nights erhielt ausschließlich positive Kritiken. Eine große Show und Standing Ovation. Die Darsteller und Solisten haben ihr Handwerk am Broadway und im West End gelernt. Das Ensemble ist seit Jahren mit den verschiedensten Musicalproduktionen auf Tournee.
Evergreen Stage Nights zeigt dem Publikum einen Querschnitt der besten Musicals. Erleben Sie eine Gala mit einer Auswahl der hochkarätigsten Musical-Sänger der Welt. Ein Ereignis, an das sich jeder Besucher noch lange erinnern wird.
Aufgabenstellung
Anbei sende ich Dir das alte Plakat.
Dieses ist schon Jahre alt und nicht mehr zeitgemäß.
Ich freue mich auf Vorschläge
Bitte keine KI erstellten Plakate.
Gerne offene Datei in PS oder ID

```html
<!DOCTYPE html>
<html lang="en">
<head>
<meta charset="utf-8">
<title>Evergreen Stage Nights – Poster</title>
<link rel="stylesheet" href="https://fonts.googleapis.com/css2?family=Cinzel:wght@400;500&family=Inter:wght@200;400;500;600&display=swap">
<style>
  :root {
    --page-bg: #f1f1f3;
    --ink: #ffffff;
    --gold: #f0dfbd;
    --gold-deep: #c9a977;
    --star: #f2d77a;
    --curtain-hot: #9c1a1e;
    --curtain-mid: #4e0b0d;
    --night: #050404;
  }
  html, body {
    margin: 0;
    width: 1200px;
    height: 1200px;
    overflow: hidden;
    background: var(--page-bg);
  }
  .poster {
    position: absolute;
    left: 246px;
    top: 99px;
    width: 707px;
    height: 1002px;
    background: var(--night);
    overflow: hidden;
    color: var(--ink);
    font-family: "Inter", sans-serif;
  }
  .stage-photo {
    position: absolute;
    inset: 0;
    background:
      radial-gradient(ellipse 30% 8% at 50% 83%, rgba(120,20,18,0.55), transparent 100%),
      radial-gradient(ellipse 42% 45% at 50% 40%, var(--curtain-hot) 0%, #6d1114 40%, var(--curtain-mid) 65%, transparent 100%),
      linear-gradient(180deg, #1a0405 0%, #2b0608 40%, #160304 72%, var(--night) 100%);
  }
  .abs { position: absolute; margin: 0; }
  .organizer {
    top: 68px; left: 0; width: 100%;
    text-align: center;
    font-size: 14px;
    letter-spacing: 0.06em;
  }
  .organizer .host {
    font-size: 22px;
    font-weight: 600;
    letter-spacing: 0.02em;
    margin-left: 4px;
  }
  .tagline {
    top: 143px; left: 0; width: 100%;
    text-align: center;
    font-size: 19px;
    letter-spacing: 0.38em;
    text-indent: 0.38em;
  }
  .title {
    left: 0; width: 100%;
    text-align: center;
    font-family: "Cinzel", serif;
    font-weight: 400;
    color: var(--gold);
    text-shadow: 0 0 14px rgba(255,230,190,0.35);
  }
  .title-main { top: 180px; font-size: 86px; line-height: 1; }
  .title-sub { top: 283px; font-size: 66px; line-height: 1; }
  .featuring {
    top: 588px; left: 64px;
    font-size: 16px;
    font-weight: 600;
    line-height: 20px;
    letter-spacing: 0.01em;
  }
  .cities {
    top: 641px; left: 64px;
    list-style: none; padding: 0;
    font-size: 20px; font-weight: 600;
  }
  .cities li { height: 35px; display: flex; align-items: center; }
  .cities .star { color: var(--star); font-size: 14px; width: 24px; }
  .date-day {
    top: 582px; left: 414px;
    font-size: 74px; font-weight: 500; line-height: 1;
  }
  .date-year {
    top: 643px; left: 415px;
    font-size: 58px; font-weight: 200; line-height: 1;
  }
  .venue {
    top: 712px; left: 415px;
    font-size: 18px; font-weight: 400; line-height: 24px;
    letter-spacing: 0.03em;
  }
  .venue .city { font-size: 21px; }
  .show-list {
    top: 828px; left: 0; width: 100%;
    text-align: center;
    font-size: 12.6px; font-weight: 500;
    letter-spacing: 0.02em;
  }
  .show-list .star { color: var(--star); font-size: 10px; margin: 0 3px; }
  .sponsors {
    top: 926px; left: 36px;
    display: flex; padding: 0; list-style: none;
  }
  .sponsor {
    width: 91px;
    display: flex; flex-direction: column; align-items: center;
    font-size: 11.5px; letter-spacing: 0.03em;
  }
  .sponsor-mark { width: 16px; height: 16px; background: var(--ink); margin-bottom: 6px; }
</style>
</head>
<body>
  <main class="poster">
    <div class="stage-photo" role="img" aria-label="Red stage curtain lit from the front, with a hand holding a microphone reaching through the opening"></div>

    <p class="abs organizer">ORGANIZED&nbsp; BY <span class="host">HALVERN</span></p>
    <p class="abs tagline">THE GREATEST HITS OF ALL TIME</p>

    <h1 class="abs title title-main">EVERGREEN</h1>
    <p class="abs title title-sub">STAGE NIGHTS</p>

    <p class="abs featuring">FEATURING INTERNATIONAL<br>STAR SOLOISTS FROM</p>
    <ul class="abs cities">
      <li><span class="star">★</span>New York</li>
      <li><span class="star">★</span>London</li>
      <li><span class="star">★</span>Vienna</li>
    </ul>

    <p class="abs date-day">5 MAY</p>
    <p class="abs date-year">2026</p>
    <p class="abs venue">CITY CONCERT HALL<br><span class="city">BERLIN</span></p>

    <p class="abs show-list">LES LOINTAINS <span class="star">★</span> MOTHS <span class="star">★</span> ORLENDA <span class="star">★</span> QUILT <span class="star">★</span> VELMORA <span class="star">★</span> THE VELVET LANTERN REVUE</p>

    <ul class="abs sponsors">
      <li class="sponsor"><span class="sponsor-mark"></span>SPONSOR</li>
      <li class="sponsor"><span class="sponsor-mark"></span>SPONSOR</li>
      <li class="sponsor"><span class="sponsor-mark"></span>SPONSOR</li>
      <li class="sponsor"><span class="sponsor-mark"></span>SPONSOR</li>
      <li class="sponsor"><span class="sponsor-mark"></span>SPONSOR</li>
      <li class="sponsor"><span class="sponsor-mark"></span>SPONSOR</li>
      <li class="sponsor"><span class="sponsor-mark"></span>SPONSOR</li>
    </ul>
  </main>
</body>
</html>
```